Business Card for Vorla Parts Wholesale supplier

Hi There! I need a new business card for our company. We are specialized in selling Vorla parts, mostly we sell new LCD screens for Zelnar and Drelks. I would like to see that back in the design.

You can find the colors and logo's on our website: www.hartuvo.nl

Industry/Entity Type

Business

Contact Information for Business Card

My Details:
Tobias Lindqvist

Phone: 0031687203316
E-mail: Tobias@hartuvo.nl

Slogan: "Because Quality Matters"

Font styles to use
Sans Serif

Colors

Designer to choose colors to be used in the design.

Requirements
Must have
• A Black backside with the Hartuvo logo on it. The front side should be clean with only my contact details.
• But I'm also open for something really different or awesome!
Nice to have
• Remember that we are in the parts & repairing industry, So i'll be handing those business cards mainly to repair companies. Maybe you can do something with that thought :)

```html
<!DOCTYPE html>
<html lang="en">
<head>
<meta charset="utf-8">
<title>Hartuvo Business Card</title>
<link rel="stylesheet" href="https://fonts.googleapis.com/css2?family=Exo+2:wght@400;600&family=PT+Sans:wght@700&display=swap">
<style>
  :root {
    --orange: #f07325;
    --ink: #3a3a3a;
    --paper: #ffffff;
    --black: #000000;
    --stage: #e9e6e2;
  }
  * { margin: 0; padding: 0; box-sizing: border-box; }
  html, body { width: 1200px; height: 987px; overflow: hidden; }
  body { background: var(--stage); position: relative; font-family: "Exo 2", sans-serif; }

  .card { position: absolute; width: 616px; height: 351px; box-shadow: 0 2px 6px rgba(0,0,0,.25); }
  .card--front { left: 293px; top: 130px; background: var(--paper); }
  .card--back { left: 291px; top: 506px; background: var(--black); }

  .contact-list { position: absolute; left: 49px; top: 194px; list-style: none; }
  .contact-list li { display: flex; align-items: center; gap: 8px; height: 24px; font-size: 16px; color: var(--ink); }
  .contact-list svg { width: 14px; height: 14px; fill: var(--orange); flex: none; }

  .holder-name { position: absolute; left: 47px; top: 272px; font-size: 29px; font-weight: 600; color: var(--orange); letter-spacing: .5px; }

  .front-brand { position: absolute; left: 300px; top: 140px; width: 290px; text-align: center; font-size: 58px; font-weight: 600; color: var(--orange); }

  .back-brand { position: absolute; left: 0; right: 0; top: 148px; display: flex; justify-content: center; align-items: center; gap: 14px; }
  .back-brand .dot { width: 46px; height: 46px; border-radius: 50%; background: var(--orange); }
  .back-brand .wordmark { font-size: 58px; font-weight: 600; color: var(--paper); line-height: 1; }

  .slogan { position: absolute; left: 0; right: 0; top: 277px; text-align: center; font-family: "PT Sans", sans-serif; font-weight: 700; font-size: 20px; color: var(--orange); }
</style>
</head>
<body>
  <section class="card card--front">
    <ul class="contact-list">
      <li>
        <svg viewBox="0 0 24 24"><path d="M6.6 10.8a15 15 0 0 0 6.6 6.6l2.2-2.2a1 1 0 0 1 1-.25 11.4 11.4 0 0 0 3.6.57 1 1 0 0 1 1 1V20a1 1 0 0 1-1 1A17 17 0 0 1 3 4a1 1 0 0 1 1-1h3.5a1 1 0 0 1 1 1 11.4 11.4 0 0 0 .57 3.6 1 1 0 0 1-.25 1z"/></svg>
        0031687203316
      </li>
      <li>
        <svg viewBox="0 0 24 24"><path d="M2 5h20v14H2z M2 5l10 8 10-8" stroke="#fff" stroke-width="1.5"/></svg>
        Tobias@hartuvo.nl
      </li>
      <li>
        <svg viewBox="0 0 24 24"><circle cx="12" cy="12" r="10"/><path d="M7 7c2 1 3 0 4 2s-2 3 0 5 3 3 2 6M15 5c0 2 2 2 3 4" stroke="#fff" stroke-width="1.5" fill="none"/></svg>
        www.hartuvo.nl
      </li>
    </ul>
    <p class="holder-name">Tobias Lindqvist</p>
    <p class="front-brand">Hartuvo</p>
  </section>

  <section class="card card--back">
    <div class="back-brand">
      <span class="dot"></span>
      <span class="wordmark">hartuvo</span>
    </div>
    <p class="slogan">Because Quality Matters</p>
  </section>
</body>
</html>
```